professional business card design

Business card design. Photos have been uploaded and i am open to the designer choosing which photos to use. Would like the card to be mostyly in a grey scale design with black, whites, silver & grey colours. I have added copy of our flyer as would like on the back side of card our services to be listed. Do not use any bright colurs such as blue red green or yellow. i need to be able to edit the phone number and naem in the final card design submitted.

Target Market(s)

Clients

Industry/Entity Type

earhmovibng and transport

Contact Information for Business Card

Director Name, address, email, phone number and services

Colors

Designer to choose only greyscale colors for use in the design.

Requirements
Should not have
• no yellow, red, blue or green

```html
<!DOCTYPE html>
<html lang="en">
<head>
<meta charset="utf-8">
<title>Varnesk Business Card</title>
<link href="https://fonts.googleapis.com/css2?family=Arimo:wght@400;700&display=swap" rel="stylesheet">
<style>
  :root {
    --page: #2a2a2a;
    --card: #101010;
    --card-edge: #1c1c1c;
    --white: #ffffff;
    --silver: #d4d4d4;
    --grey: #9a9a9a;
    --rule: #4a4a4a;
  }
  * { margin: 0; padding: 0; box-sizing: border-box; }
  html, body { width: 1200px; height: 900px; overflow: hidden; }
  body {
    background: var(--page);
    font-family: "Arimo", Arial, sans-serif;
    color: var(--white);
    position: relative;
  }
  .card {
    position: absolute;
    left: 250px;
    width: 700px;
    height: 400px;
    background: radial-gradient(ellipse at 40% 50%, var(--card-edge) 0%, var(--card) 75%);
    overflow: hidden;
  }
  .card--front { top: 30px; }
  .card--back { top: 470px; }

  /* Front */
  .brand {
    position: absolute;
    font-weight: 700;
    color: var(--silver);
    letter-spacing: 1px;
    white-space: nowrap;
  }
  .card--front .brand { left: 60px; top: 240px; font-size: 44px; }
  .divider {
    position: absolute;
    left: 350px; top: 70px;
    width: 1px; height: 280px;
    background: var(--rule);
  }
  .contact { position: absolute; left: 380px; top: 70px; }
  .contact__name { font-size: 26px; font-weight: 700; line-height: 1; }
  .contact__role { font-size: 17px; color: var(--grey); margin-top: 4px; }
  .contact__list { list-style: none; margin-top: 18px; }
  .contact__item {
    display: flex; align-items: center; gap: 8px;
    font-size: 18px; color: var(--silver); line-height: 1.45;
  }
  .contact__item svg { width: 16px; height: 16px; flex: none; }
  .company { margin-top: 16px; }
  .company__name { font-size: 19px; font-weight: 700; }
  .company__address { font-size: 18px; color: var(--grey); line-height: 1.3; margin-top: 2px; }

  /* Back */
  .services { position: absolute; left: 40px; top: 36px; }
  .services__title { font-size: 18px; font-weight: 700; margin-bottom: 6px; }
  .services__list { list-style: none; }
  .services__item {
    font-size: 16px; color: var(--silver); line-height: 1.33;
    padding-left: 16px; position: relative;
  }
  .services__item::before {
    content: ""; position: absolute; left: 0; top: 7px;
    width: 7px; height: 7px; border-radius: 50%; background: var(--white);
  }
  .services__note {
    margin-top: 14px; font-size: 16px; color: var(--grey); line-height: 1.3; width: 400px;
  }
  .services__note strong { color: var(--white); font-weight: 400; }
  .card--back .brand { right: 40px; top: 40px; font-size: 40px; }
  .truck-photo {
    position: absolute; right: 20px; top: 110px;
    width: 260px; height: 190px;
    background: linear-gradient(135deg, #3a3a3a 0%, #888 45%, #cfcfcf 70%, #1a1a1a 100%);
  }
</style>
</head>
<body>
  <section class="card card--front">
    <div class="brand">VARNESK</div>
    <div class="divider"></div>
    <div class="contact">
      <div class="contact__name">NAME HERE</div>
      <div class="contact__role">Managing Director</div>
      <ul class="contact__list">
        <li class="contact__item">
          <svg viewBox="0 0 16 16"><path d="M3 1l3 1 1 3-2 1.5a9 9 0 0 0 4.5 4.5L11 9l3 1 1 3-2 2C7 15 1 9 1 3z" fill="var(--white)"/></svg>
          000 123 456
        </li>
        <li class="contact__item">
          <svg viewBox="0 0 16 16"><rect x="1" y="3" width="14" height="10" fill="var(--white)"/><path d="M1 3l7 6 7-6" fill="none" stroke="var(--card)" stroke-width="1.5"/></svg>
          email@website.com
        </li>
        <li class="contact__item">
          <svg viewBox="0 0 16 16"><circle cx="8" cy="8" r="7" fill="none" stroke="var(--white)" stroke-width="1.5"/><path d="M1 8h14M8 1c-3 3-3 11 0 14M8 1c3 3 3 11 0 14" fill="none" stroke="var(--white)" stroke-width="1.2"/></svg>
          www.websiteaddress.com
        </li>
      </ul>
      <div class="company">
        <div class="company__name">VARNESK PTY LTD</div>
        <div class="company__address">Address Line Here, Address<br>line goes here pincode.</div>
      </div>
    </div>
  </section>

  <section class="card card--back">
    <div class="services">
      <div class="services__title">OUR SERVICES</div>
      <ul class="services__list">
        <li class="services__item">Over size loads/hot shot loads</li>
        <li class="services__item">Heavy vehicle recovery services</li>
        <li class="services__item">Potable water deliveries</li>
        <li class="services__item">Road building/maintenance</li>
        <li class="services__item">Earthworks</li>
        <li class="services__item">Sand &amp; metal supply &amp; cartage</li>
        <li class="services__item">Road train tippers</li>
        <li class="services__item">Road train tankers</li>
        <li class="services__item">Road train flat tops</li>
        <li class="services__item">Drop deck trailers</li>
        <li class="services__item">Mine site accredited</li>
        <li class="services__item">Equipment &amp; operators</li>
      </ul>
      <p class="services__note">We offer a large range of services not listed so <strong>Call us today for a personalised quote to suit your needs.</strong></p>
    </div>
    <div class="brand">VARNESK</div>
    <div class="truck-photo" role="img" aria-label="Black and white photo of a road train truck with bull bar and trailer"></div>
  </section>
</body>
</html>
```